Harbourline Electrical Solutions

On one side. LOGO (underneath:) Commercial Industrial Residential

- NAME & CONTACT DETAILS

Marcus T. Hollings
Project Manager

(Cell icon) (441) 555-0187
(Email icon) hlelectricalsolutions@mailvento.com
(Facebook & Instagram icons )@hlelectricalsolutions

Other side: LOGO - underneath ELECTRICAL CONSTRUCTION & MAINTENANCE . LED LIGHTING & AUTOMATION . LIFE SAFETY SYSTEMS (FIRE ALARM / SECURITY) . DATA & COMMUNICATION

```html
<!DOCTYPE html>
<html lang="en">
<head>
<meta charset="utf-8">
<title>Harbourline Electrical Solutions – Business Card</title>
<link rel="stylesheet" href="https://fonts.googleapis.com/css2?family=Work+Sans:wght@400;500;600;700&display=swap">
<style>
  :root {
    --page-bg: #d9d9d9;
    --card-bg: #1c1c1c;
    --ink: #ffffff;
    --ink-soft: #e6e6e6;
    --logo-grey: #a8a8a8;
    --rule: #ffffff;
  }
  * { box-sizing: border-box; margin: 0; padding: 0; }
  html, body {
    width: 1200px; height: 900px; overflow: hidden;
    background: var(--page-bg);
    font-family: "Work Sans", Arial, sans-serif;
  }
  .sheet {
    width: 1200px; height: 900px;
    display: flex; flex-direction: column; align-items: center; justify-content: center;
    gap: 44px;
  }
  .card {
    position: relative;
    width: 640px; height: 366px;
    background: var(--card-bg);
    border-radius: 18px;
    color: var(--ink);
    box-shadow: 0 10px 28px rgba(0,0,0,0.25);
  }

  /* Services side */
  .card--services .brand {
    position: absolute; left: 250px; top: 58px;
    display: flex; align-items: center; gap: 16px;
  }
  .brand__mark {
    width: 14px; height: 14px; background: var(--logo-grey);
  }
  .brand__name {
    font-weight: 500; text-transform: uppercase;
    color: var(--logo-grey);
    font-size: 24px; line-height: 1.05; letter-spacing: 3px;
  }
  .services {
    position: absolute; left: 120px; top: 182px;
    list-style: none;
  }
  .services li {
    font-weight: 600; text-transform: uppercase;
    font-size: 17px; letter-spacing: 1.6px; line-height: 25px;
    padding-left: 22px; position: relative;
  }
  .services li::before {
    content: ""; position: absolute; left: 0; top: 9px;
    width: 7px; height: 7px; border-radius: 50%; background: var(--ink);
  }

  /* Contact side */
  .card--contact .brand {
    position: absolute; left: 46px; top: 46px;
    display: flex; align-items: center; gap: 12px;
  }
  .card--contact .brand__mark { width: 11px; height: 11px; background: var(--ink); }
  .card--contact .brand__name {
    color: var(--ink); font-size: 15px; letter-spacing: 2.4px; font-weight: 600;
  }
  .social {
    position: absolute; left: 38px; top: 208px; width: 270px;
    font-size: 16px; letter-spacing: 0.4px; color: var(--ink-soft);
    padding-bottom: 8px; border-bottom: 1.5px solid var(--rule);
  }
  .person {
    position: absolute; right: 44px; top: 222px; width: 330px;
    text-align: right;
  }
  .person__name {
    font-weight: 600; font-size: 21px; letter-spacing: 2.2px; text-transform: uppercase;
  }
  .person__role {
    font-size: 16px; letter-spacing: 0.8px; color: var(--ink-soft);
    padding-bottom: 10px; border-bottom: 1.5px solid var(--rule);
    margin-bottom: 10px;
  }
  .contact-line {
    display: flex; justify-content: flex-end; align-items: center; gap: 10px;
    font-size: 16px; letter-spacing: 0.3px; line-height: 26px;
  }
  .contact-line svg { width: 15px; height: 15px; flex: none; }
</style>
</head>
<body>
<main class="sheet">

  <section class="card card--services" aria-label="Card side with services">
    <div class="brand">
      <span class="brand__mark"></span>
      <p class="brand__name">Harbourline<br>Electrical<br>Solutions</p>
    </div>
    <ul class="services">
      <li>Data &amp; Communication</li>
      <li>LED Lighting &amp; Automation</li>
      <li>Electrical Construction &amp; Maintenance</li>
      <li>Life Safety Systems (Fire Alarm / Security)</li>
    </ul>
  </section>

  <section class="card card--contact" aria-label="Card side with contact details">
    <div class="brand">
      <span class="brand__mark"></span>
      <p class="brand__name">Harbourline<br>Electrical<br>Solutions</p>
    </div>

    <p class="social">@hlelectricalsolutions</p>

    <div class="person">
      <h1 class="person__name">Marcus T. Hollings</h1>
      <p class="person__role">Project Manager</p>
      <p class="contact-line">(441) 555-0187
        <svg viewBox="0 0 24 24" fill="none" stroke="#fff" stroke-width="2" stroke-linejoin="round" aria-hidden="true">
          <path d="M5 3h4l2 5-2.5 1.5a11 11 0 0 0 6 6L16 13l5 2v4a2 2 0 0 1-2 2A16 16 0 0 1 3 5a2 2 0 0 1 2-2z"/>
        </svg>
      </p>
      <p class="contact-line">hlelectricalsolutions@mailvento.com
        <svg viewBox="0 0 24 24" fill="none" stroke="#fff" stroke-width="2" stroke-linejoin="round" aria-hidden="true">
          <rect x="3" y="5" width="18" height="14" rx="1"/>
          <path d="M3 6l9 7 9-7"/>
        </svg>
      </p>
    </div>
  </section>

</main>
</body>
</html>
```